Design a website for a quickly growing ghostwriting and editing firm

DWB Productions has a website through Wix, but we need help! We are based in Austin, TX, and we work primarily with self-help, wellness, and diet authors. We offer ghostwriting, editing and book development services. You can see our basic site now at www.dorawhitbyproductions.com

```html
<!DOCTYPE html>
<html lang="en">
<head>
<meta charset="utf-8">
<title>DWB Productions — Ghostwriting, Editing &amp; Book Development</title>
<link href="https://fonts.googleapis.com/css2?family=Montserrat:wght@600;700&family=Roboto:wght@400;500;700&display=swap" rel="stylesheet">
<style>
:root{
  --orange:#f28a12;
  --orange-dark:#e07b05;
  --ink:#1f1f1f;
  --text:#555;
  --muted:#777;
  --white:#fff;
  --footer:#262626;
  --line:#555;
}
*{box-sizing:border-box;margin:0;padding:0}
html,body{width:1200px;height:4107px;overflow:hidden}
body{font-family:'Roboto',sans-serif;color:var(--text);background:var(--white);position:relative}
.wrap{width:976px;margin:0 auto;position:relative}
h1,h2,h3{font-family:'Montserrat',sans-serif;color:var(--ink);text-transform:uppercase}
.btn{display:inline-flex;align-items:center;justify-content:center;background:var(--orange);color:var(--white);font:700 15px 'Roboto',sans-serif;text-transform:uppercase;border-radius:26px;text-decoration:none;white-space:nowrap}

/* top bar */
.topbar{height:43px;background:var(--orange);color:var(--white);font-size:15px}
.topbar .wrap{display:flex;align-items:center;height:43px}
.topbar .info{display:flex;align-items:center;gap:10px}
.topbar .sep{margin:0 16px;opacity:.8}
.social{display:flex;gap:8px;margin-left:auto}
.social span{width:34px;height:34px;border:2px solid var(--white);border-radius:50%}

/* nav */
.nav{height:91px;border-bottom:1px solid #eee}
.nav .wrap{display:flex;align-items:center;height:91px}
.brand{display:flex;align-items:center;gap:10px;font:600 22px 'Montserrat',sans-serif;color:#333;white-space:nowrap}
.brand i{width:60px;height:60px;border-radius:50%;background:#d9a36b;display:block;flex:none}
.menu{display:flex;gap:23px;margin-left:40px;font-size:15px;color:#222;text-transform:uppercase;white-space:nowrap}
.nav .btn{margin-left:auto;width:141px;height:50px}

/* hero */
.hero{position:relative;height:599px;background:linear-gradient(120deg,#c9a25f 0%,#e6b464 35%,#f3d7a2 60%,#9a8a74 100%)}
.hero-box{position:absolute;left:279px;top:190px;width:642px;height:220px;background:rgba(255,255,255,.35);text-align:center;padding-top:20px}
.hero-box h1{font-size:33px;color:#1c1c1c;letter-spacing:.3px}
.hero-box p{font-size:16px;color:#333;font-weight:500;line-height:27px;margin:14px auto 0;width:500px}
.hero-box .btn{width:167px;height:48px;margin-top:18px}
.arrow{position:absolute;top:50%;transform:translateY(-50%)}

/* about */
.about{position:absolute;top:829px;left:0;width:1200px;height:410px}
.about .photo{position:absolute;left:0;top:0;width:552px;height:410px;background:linear-gradient(135deg,#eceae6,#c9c3bd 55%,#a3353a 80%,#d8d2cc)}
.about-copy{position:absolute;left:601px;top:20px;width:490px;text-align:left}
.about-copy h2{font-size:34px}
.about-copy p{font-size:13.5px;line-height:25px;text-align:justify;margin-top:18px;color:var(--muted)}
.about-copy .btn{width:142px;height:48px;margin-top:30px}

/* services */
.services{position:absolute;top:1334px;left:0;width:1200px;height:593px;background:linear-gradient(180deg,#4a3a30,#2e241f 60%,#3b2f27);color:var(--white);text-align:center}
.services h2{color:var(--white);font-size:34px;padding-top:54px}
.lead{font-size:14.5px;line-height:25px;width:870px;margin:14px auto 0}
.svc-cols{display:flex;gap:36px;width:976px;margin:64px auto 0;text-align:left}
.svc{width:301px}
.svc h3{font:700 19px 'Roboto',sans-serif;color:var(--white);margin-top:18px}
.svc p{font-size:13.5px;line-height:23px;text-align:justify;margin-top:16px;color:#eee}
.services .btn{width:142px;height:46px;margin-top:40px}

/* work with */
.work{position:absolute;top:1990px;left:0;width:1200px;text-align:center}
.work h2{font-size:34px}
.work .lead{color:var(--muted)}
.cards{display:flex;gap:25px;width:976px;margin:44px auto 0}
.card{width:309px;height:373px;position:relative;flex:none}
.card.photo1{background:linear-gradient(160deg,#4a4a4a,#8d8f96 55%,#5b6f86)}
.card.photo2{background:linear-gradient(180deg,#d7d0c6,#a99a8a 60%,#4a4440)}
.card .label{position:absolute;left:0;right:0;bottom:28px;text-align:center;color:var(--white);font:700 20px 'Roboto',sans-serif}
.card.dark{background:#2d2a28;color:#eee;padding:44px 22px 0}
.card.dark h3{color:var(--orange);font:700 20px 'Roboto',sans-serif;margin-top:18px}
.card.dark p{font-size:14px;line-height:24px;margin-top:16px}
.card.dark a{display:inline-flex;align-items:center;gap:8px;color:var(--orange);font-weight:700;font-size:15px;text-decoration:none;margin-top:20px}

/* testimonials */
.testi{position:absolute;top:2633px;left:0;width:1200px;height:435px;background:linear-gradient(135deg,#f59a28,#ee8410 60%,#f39a2a)}
.testi h2{color:var(--white);text-align:center;font-size:34px;padding-top:60px}
.quote{position:absolute;left:320px;top:142px;width:609px;height:230px;background:var(--white);border-radius:30px;padding:22px 24px 0 98px}
.avatar{position:absolute;left:-46px;top:67px;width:92px;height:92px;border-radius:50%;background:linear-gradient(#c9b6a6,#7a5b4a);border:3px solid #f0d9c0}
.mark{position:absolute;left:52px;top:36px;font:700 80px/1 'Montserrat',sans-serif;color:#f5cc99}
.stars{display:flex;gap:4px}
.quote h3{font:500 21px/29px 'Roboto',sans-serif;color:#222;text-transform:none;margin-top:6px}
.quote p{font-size:14px;line-height:24px;color:var(--muted);margin-top:8px}
.who{margin-top:10px;font-size:14px;color:#222}
.who b{color:var(--orange);font-size:19px;font-weight:500}

/* blog */
.blog{position:absolute;top:3150px;left:0;width:1200px}
.blog h2{text-align:center;font-size:34px}
.post{position:absolute;background:var(--white);box-shadow:0 2px 10px rgba(0,0,0,.12)}
.post.big{left:112px;top:91px;width:478px;height:430px}
.post.big .img{height:274px;background:linear-gradient(135deg,#dcd6cd,#bcb2a5 50%,#8e8ba5)}
.post .date{display:inline-block;background:var(--orange);color:var(--white);font-size:12px;font-weight:700;padding:6px 12px}
.post.big .date{position:absolute;left:40px;top:262px}
.post h3{font:500 16.5px/27px 'Roboto',sans-serif;color:#222}
.post p{font-size:14px;line-height:23px;color:var(--muted);margin-top:10px}
.post.big .body{padding:36px 16px 0 40px}
.post.small{left:609px;width:480px;height:202px;display:flex}
.post.small .img{width:190px;height:100%;flex:none}
.post.small .body{padding:22px 8px 0 21px}
.post.small h3{margin-top:20px}
.post.s1{top:91px}.post.s1 .img{background:linear-gradient(135deg,#e8e4de,#8f8a84 60%,#f1eee9)}
.post.s2{top:320px}.post.s2 .img{background:linear-gradient(135deg,#9a7b5a,#d8a050 45%,#7a8a88)}

/* footer */
.footer{position:absolute;top:3767px;left:0;width:1200px;height:340px;background:var(--footer);color:#eee}
.footer .brand{position:absolute;left:112px;top:54px;color:#eee;font-size:22px}
.footer .brand i{background:#8e8e8e}
.fsocial{position:absolute;left:140px;top:165px;display:flex;gap:8px}
.fsocial span{width:34px;height:34px;border-radius:50%;background:var(--orange)}
.fcol{position:absolute;top:56px}
.fcol h4{color:var(--orange);font:700 16px 'Roboto',sans-serif;text-transform:uppercase;margin-bottom:14px}
.fcol li{list-style:none;font-size:15px;line-height:25px}
.contact li{display:flex;align-items:center;gap:16px;margin-bottom:18px;line-height:21px}
.contact .ic{width:38px;height:38px;border:2px solid var(--orange);border-radius:50%;display:flex;align-items:center;justify-content:center;flex:none}
.fline{position:absolute;left:112px;top:275px;width:976px;height:1px;background:var(--line)}
.legal{position:absolute;top:302px;left:0;width:100%;text-align:center;font-size:12px}
</style>
</head>
<body>

<header class="topbar">
  <div class="wrap">
    <div class="info">
      <svg width="12" height="12" viewBox="0 0 24 24" fill="#fff"><path d="M6.6 10.8a15 15 0 0 0 6.6 6.6l2.2-2.2a1 1 0 0 1 1-.25 11.4 11.4 0 0 0 3.6.57 1 1 0 0 1 1 1V20a1 1 0 0 1-1 1A17 17 0 0 1 3 4a1 1 0 0 1 1-1h3.5a1 1 0 0 1 1 1c0 1.25.2 2.45.57 3.6a1 1 0 0 1-.25 1z"/></svg>
      <span>123-456-7890</span>
      <span class="sep">|</span>
      <svg width="10" height="14" viewBox="0 0 10 14" fill="#fff"><path d="M5 0a5 5 0 0 0-5 5c0 3.8 5 9 5 9s5-5.2 5-9a5 5 0 0 0-5-5zm0 7a2 2 0 1 1 0-4 2 2 0 0 1 0 4z"/></svg>
      <span>Austin, Texas</span>
    </div>
    <div class="social"><span></span><span></span><span></span><span></span></div>
  </div>
</header>

<nav class="nav">
  <div class="wrap">
    <div class="brand"><i></i>DWB Productions</div>
    <div class="menu"><span>Home</span><span>About Us</span><span>Our Services</span><span>We Work With</span><span>Latest Blog</span></div>
    <a class="btn">Contact Us</a>
  </div>
</nav>

<section class="hero" role="img" aria-label="Writer with a fountain pen at a desk beside a laptop in warm light">
  <svg class="arrow" style="left:74px" width="40" height="50" viewBox="0 0 40 50"><path d="M30 5 10 25l20 20" fill="none" stroke="#f28a12" stroke-width="6"/></svg>
  <svg class="arrow" style="right:74px" width="40" height="50" viewBox="0 0 40 50"><path d="M10 5l20 20-20 20" fill="none" stroke="#fff" stroke-width="6"/></svg>
  <div class="hero-box">
    <h1>Welcome to DWB Productions</h1>
    <p>Lorem ipsum dolor sit amet, consectetur adipiscing elit, sed do eiusmod tempor incididunt ut labore.</p>
    <a class="btn">See Our Works</a>
  </div>
</section>

<section class="about">
  <div class="photo" role="img" aria-label="Young woman in a red hoodie writing notes beside a laptop"></div>
  <div class="about-copy">
    <h2>About Us</h2>
    <p>Lorem ipsum dolor sit amet, consectetur adipiscing elit, sed do eiusmod tempor incididunt ut labore et dolore magna aliqua ut enim ad minim ven iam, quis nostrud exercitation ullamco laboris nisi ut aliquip ex ea commo do consequat. Duis aute irure dolor in reprehenderit in voluptate velit esse cillum dolore eu fugiat nulla pariatur.</p>
    <p>Sed ut perspiciatis unde omnis iste natus error sit voluptatem accusantium doloremque laudantium, totam rem aperiam, eaque ipsa quae ab illo inventore veritatis et quasi architecto beatae.</p>
    <a class="btn">Learn More</a>
  </div>
</section>

<section class="services" aria-label="Our services; background of open books on a table">
  <h2>Our Services</h2>
  <p class="lead">Lorem ipsum dolor sit amet, consectetur adipiscing elit, sed do eiusmod tempor incididunt ut labore et dolore magna aliqua ut enim ad minim venscing elit, sed do eiusmod tempor iiam, quis nostrud.</p>
  <div class="svc-cols">
    <div class="svc">
      <svg width="58" height="56" viewBox="0 0 58 56" fill="none" stroke="#f28a12" stroke-width="2"><circle cx="10" cy="10" r="7"/><rect x="20" y="12" width="34" height="40" rx="2"/><path d="M27 22h20M27 30h20M27 38h20M27 46h12"/><path d="M4 24v26h14"/></svg>
      <h3>Ghostwriting</h3>
      <p>Lorem ipsum dolor sit amet, consectetur adi piscing elit, sed do eiusmod tempor incididunt ut labore et dolore magna aliqua ut enim ad minim veniam quis nostrud.</p>
    </div>
    <div class="svc">
      <svg width="58" height="56" viewBox="0 0 58 56" fill="none" stroke="#f28a12" stroke-width="2"><rect x="4" y="6" width="36" height="46" rx="2"/><path d="M11 18h20M11 26h20M11 34h14M11 42h10"/><path d="M52 4 30 34l-4 8 8-4L56 8z"/></svg>
      <h3>Editing</h3>
      <p>Lorem ipsum dolor sit amet, consectetur adi piscing elit, sed do eiusmod tempor incididunt ut labore et dolore magna aliqua ut enim ad minim veniam quis nostrud.</p>
    </div>
    <div class="svc">
      <svg width="58" height="56" viewBox="0 0 58 56" fill="none" stroke="#f28a12" stroke-width="2"><circle cx="29" cy="12" r="9"/><path d="M26 9l-3 3 3 3M32 9l3 3-3 3"/><path d="M4 28h24v24H4zM30 28h24v24H30z"/><path d="M9 35h14M9 41h14M35 35h14M35 41h14"/></svg>
      <h3>Book Development</h3>
      <p>Lorem ipsum dolor sit amet, consectetur adi piscing elit, sed do eiusmod tempor incididunt ut labore et dolore magna aliqua ut enim ad minim veniam quis nostrud.</p>
    </div>
  </div>
  <a class="btn">Learn More</a>
</section>

<section class="work">
  <h2>We Work With</h2>
  <p class="lead">Lorem ipsum dolor sit amet, consectetur adipiscing elit, sed do eiusmod tempor incididunt ut labore et dolore magna aliqua ut enim ad minim venscing elit, sed do eiusmod tempor iiam, quis nostrud.</p>
  <div class="cards">
    <div class="card photo1" role="img" aria-label="Woman reading a book under a blanket"><span class="label">SELF-HELP</span></div>
    <div class="card photo2" role="img" aria-label="Group of women meditating in a studio"><span class="label">WELLNESS</span></div>
    <div class="card dark">
      <svg width="54" height="56" viewBox="0 0 54 56" fill="none" stroke="#f28a12" stroke-width="2"><rect x="4" y="6" width="34" height="46" rx="2"/><path d="M14 3h14v7H14z"/><path d="M11 20h4M19 20h12M11 30h4M19 30h10M11 40h4"/><circle cx="40" cy="42" r="10"/><path d="M40 32c0-4 3-6 6-6"/></svg>
      <h3>DIET AUTHORS</h3>
      <p>Sed ut perspiciatis unde omnis iste natus error sit voluptatem accusantium dolo remque laudantium, totam rem aperiam, eaque ipsa quae ab illo inventore veritatis et quasi architecto beat.</p>
      <a>LEARN MORE <svg width="14" height="14" viewBox="0 0 14 14" fill="none" stroke="#f28a12" stroke-width="2"><circle cx="7" cy="7" r="6"/><path d="M4 7h5M7 5l2 2-2 2"/></svg></a>
    </div>
  </div>
</section>

<section class="testi" aria-label="Testimonials; warm orange backdrop">
  <h2>Testimonials</h2>
  <svg class="arrow" style="left:84px;top:258px" width="30" height="50" viewBox="0 0 30 50"><path d="M24 5 6 25l18 20" fill="none" stroke="#fff" stroke-width="5"/></svg>
  <svg class="arrow" style="right:84px;top:258px" width="30" height="50" viewBox="0 0 30 50"><path d="M6 5l18 20L6 45" fill="none" stroke="#fff" stroke-width="5"/></svg>
  <div class="quote">
    <div class="avatar" role="img" aria-label="Portrait of the client"></div>
    <span class="mark">“</span>
    <div class="stars">
      <svg width="110" height="20" viewBox="0 0 110 20" fill="#f5b301"><g id="s"><path d="M10 1l2.6 6 6.4.5-4.9 4.2 1.5 6.3L10 14.6 4.4 18l1.5-6.3L1 7.5 7.4 7z"/></g><use href="#s" x="23"/><use href="#s" x="46"/><use href="#s" x="69"/><use href="#s" x="92"/></svg>
    </div>
    <h3>Lorem ipsum dolor sit amet, consectetur adipis cing elit, sed do eiusmod tempor</h3>
    <p>Sed ut perspiciatis unde omnis iste natus error sit voluptatem accusan tium doloremque laudantium, totam rem aperiam.</p>
    <div class="who"><b>MARA ELLISON,</b> AUSTIN, TX</div>
  </div>
</section>

<section class="blog">
  <h2>Latest Blog Post</h2>
  <article class="post big">
    <div class="img" role="img" aria-label="Woman reading with a cup of coffee beside a lamp"></div>
    <span class="date">08 JUL 2021</span>
    <div class="body">
      <h3>LOREM IPSUM DOLOR SIT AMET, CONSEC TETUR ADIPISCING ELITM DOLO</h3>
      <p>Sed ut perspiciatis unde omnis iste natus error sit volup tatem accusantium doloremis iste natus erroque.</p>
    </div>
  </article>
  <article class="post small s1">
    <div class="img" role="img" aria-label="Man writing in a notebook"></div>
    <div class="body">
      <span class="date">08 JUL 2021</span>
      <h3>LOREM IPSUM DOLOR SIT AMET, CONSEC TETUR ADIPI</h3>
      <p>Sed ut perspiciatis unde omnis iste na tus error sit volup tatem.</p>
    </div>
  </article>
  <article class="post small s2">
    <div class="img" role="img" aria-label="Glasses and notebook beside a plate of fruit"></div>
    <div class="body">
      <span class="date">08 JUL 2021</span>
      <h3>LOREM IPSUM DOLOR SIT AMET, CONSEC TETUR ADIPI</h3>
      <p>Sed ut perspiciatis unde omnis iste na tus error sit volup tatem.</p>
    </div>
  </article>
</section>

<footer class="footer">
  <div class="brand"><i></i>DWB Productions</div>
  <div class="fsocial"><span></span><span></span><span></span><span></span></div>
  <div class="fcol" style="left:411px">
    <h4>Quick Links</h4>
    <ul><li>Home</li><li>About Us</li><li>Our Services</li><li>We Work With</li><li>Latest Blog</li></ul>
  </div>
  <div class="fcol" style="left:610px">
    <h4>Get Connected</h4>
    <ul><li>Careers</li><li>Investors</li><li>Terms Of Service</li><li>Privacy Policy</li><li>Legal Support</li></ul>
  </div>
  <div class="fcol contact" style="left:866px">
    <h4>Quick Links</h4>
    <ul>
      <li><span class="ic"><svg width="12" height="16" viewBox="0 0 10 14" fill="#f28a12"><path d="M5 0a5 5 0 0 0-5 5c0 3.8 5 9 5 9s5-5.2 5-9a5 5 0 0 0-5-5zm0 7a2 2 0 1 1 0-4 2 2 0 0 1 0 4z"/></svg></span>456, Austin, TX<br>United States</li>
      <li><span class="ic"><svg width="15" height="15" viewBox="0 0 24 24" fill="#f28a12"><path d="M6.6 10.8a15 15 0 0 0 6.6 6.6l2.2-2.2a1 1 0 0 1 1-.25 11.4 11.4 0 0 0 3.6.57 1 1 0 0 1 1 1V20a1 1 0 0 1-1 1A17 17 0 0 1 3 4a1 1 0 0 1 1-1h3.5a1 1 0 0 1 1 1c0 1.25.2 2.45.57 3.6a1 1 0 0 1-.25 1z"/></svg></span>123-456-7890</li>
      <li><span class="ic"><svg width="16" height="12" viewBox="0 0 16 12" fill="#f28a12"><path d="M0 0h16v12H0z"/><path d="M0 0l8 6 8-6" fill="none" stroke="#262626" stroke-width="1.5"/></svg></span>info@dwbproductions.com</li>
    </ul>
  </div>
  <div class="fline"></div>
  <p class="legal">© 2021 <b>DWB PRODUCTIONS</b>. All Rights Reserved</p>
</footer>

</body>
</html>
```